Wealth management Facebook Advertisement

Hello, we are trying to capture more leads to our online booking link through Facebook advertisement. We want an attractive modern design to get more clients and catch the attention of high net-worth clients. We deal with high-net-worth retirees, business owners, farmers, and wealth transfer. We offer high-net-worth client solutions that cover Financial Planning, Retirement and Estate Planning, Investment Planning, Tax Planning, and Insurance Planning. The final design that we would be looking for is modern and eye-catching and makes the prospective clients want to click our meeting link to schedule an introductory consultation.

We are in the Wealth Management / Financial Planning industry

Our online booking link Is the following :

https://calendar.brisquelmail.com/owa/calendar/MarcusFenleyPartnersRQPrivateWealth@tovrelfinancial.net/bookings/

Our current Facebook page is the following:

https://www.plorvenet.com/FenleyPrivateWealth

Please ask any further questions for needed information for creating design

```html
<!DOCTYPE html>
<html lang="en">
<head>
<meta charset="utf-8">
<title>RQ Private Wealth Management – Facebook Ad</title>
<link rel="stylesheet" href="https://fonts.googleapis.com/css2?family=Poppins:wght@400;500;600;700;800&display=swap">
<style>
  :root {
    --navy: #0b1c4d;
    --navy-deep: #050d2a;
    --sky: #45b2f5;
    --sky-light: #55cdfb;
    --brand-blue: #1e7fd6;
    --grey-text: #444444;
    --panel-grey: #edeef0;
    --white: #ffffff;
    --photo-tone-a: #c9bfb2;
    --photo-tone-b: #8f98b0;
  }
  * { margin: 0; padding: 0; box-sizing: border-box; }
  html, body { width: 1200px; height: 1200px; overflow: hidden; background: var(--white); }
  body { font-family: "Poppins", sans-serif; }
  .ad { position: relative; width: 1200px; height: 1200px; background: var(--white); }
  .ad-shapes { position: absolute; inset: 0; }

  .brand { position: absolute; left: 80px; top: 64px; }
  .brand-row { display: flex; align-items: center; gap: 14px; }
  .brand-mark { width: 26px; height: 26px; background: var(--navy); }
  .brand-name { font-weight: 600; font-size: 31px; line-height: 1.05; color: var(--navy); }
  .brand-team { margin: 14px 0 0 40px; font-weight: 600; font-size: 34px; line-height: 1.08; color: var(--brand-blue); }

  .headline { position: absolute; left: 80px; top: 282px; font-weight: 700; text-transform: uppercase; }
  .headline-intro { font-size: 42px; line-height: 50px; color: var(--grey-text); letter-spacing: -0.5px; }
  .headline-accent { font-size: 68px; line-height: 68px; margin-top: 2px; color: var(--sky); font-weight: 800; letter-spacing: -1px; }
  .headline-strong { font-size: 68px; line-height: 72px; color: var(--navy); font-weight: 800; letter-spacing: -1px; }

  .industry { position: absolute; left: 82px; top: 554px; padding-left: 18px; border-left: 6px solid var(--sky);
    font-weight: 600; font-size: 23px; line-height: 29px; color: var(--navy); }

  .clients { position: absolute; left: 80px; top: 672px; }
  .clients-title { font-weight: 700; font-size: 42px; color: var(--sky); line-height: 50px; }
  .clients-list { list-style: none; margin-top: 20px; }
  .clients-list li { display: flex; align-items: center; gap: 14px; font-weight: 500; font-size: 27px; line-height: 41px; color: var(--navy-deep); }
  .tick { width: 24px; height: 24px; flex: none; }

  .offer-head { position: absolute; left: 597px; top: 676px; display: flex; align-items: center; gap: 12px; }
  .offer-title { font-weight: 700; font-size: 44px; color: var(--white); line-height: 1; }
  .offer-sub { font-weight: 700; font-size: 16px; line-height: 18px; color: var(--navy-deep); text-transform: uppercase; }

  .services { position: absolute; left: 494px; top: 776px; width: 706px; display: flex; }
  .service { flex: 1; display: flex; flex-direction: column; align-items: center; text-align: center;
    color: var(--white); font-weight: 600; font-size: 18px; line-height: 22px; padding-top: 2px; }
  .service + .service { border-left: 1px solid rgba(69,178,245,0.55); }
  .service-icon { width: 44px; height: 44px; margin-bottom: 10px; }

  .booking { position: absolute; left: 71px; top: 975px; width: 1069px; }
  .booking-title { font-weight: 700; font-size: 30px; color: var(--sky); line-height: 40px; padding-left: 4px; }
  .booking-link { margin-top: 6px; height: 38px; border-radius: 14px; background: var(--navy-deep); color: var(--white);
    font-weight: 500; font-size: 15px; line-height: 38px; padding-left: 12px; letter-spacing: -0.1px; white-space: nowrap; }

  .contact { position: absolute; left: 71px; top: 1090px; width: 1069px; display: flex; align-items: center; }
  .social { display: flex; align-items: center; gap: 8px; font-weight: 500; font-size: 19px; color: var(--navy-deep); }
  .social-dot { width: 34px; height: 34px; border-radius: 50%; background: var(--brand-blue); }
  .contact-divider { width: 2px; height: 34px; background: var(--sky); margin: 0 22px; }
  .website { font-weight: 500; font-size: 27px; letter-spacing: 4px; color: var(--navy-deep); white-space: nowrap; }
  .website span { color: var(--sky); }
</style>
</head>
<body>
<main class="ad">
  <svg class="ad-shapes" width="1200" height="1200" viewBox="0 0 1200 1200">
    <defs>
      <linearGradient id="skyGradient" x1="0" y1="0" x2="1" y2="0">
        <stop offset="0" stop-color="#45adf5"/>
        <stop offset="1" stop-color="#55d0fb"/>
      </linearGradient>
      <linearGradient id="navyGradient" x1="0" y1="0" x2="1" y2="0">
        <stop offset="0" stop-color="#030a24"/>
        <stop offset="1" stop-color="#0c1a52"/>
      </linearGradient>
      <linearGradient id="photoGradient" x1="0" y1="0" x2="1" y2="1">
        <stop offset="0" stop-color="#d8cfc3"/>
        <stop offset="0.55" stop-color="#b3a89a"/>
        <stop offset="1" stop-color="#8e97ae"/>
      </linearGradient>
    </defs>
    <polygon class="client-panel" points="0,654 530,654 407,939 0,939" fill="var(--panel-grey)"/>
    <polygon class="accent-band" points="822,0 1200,0 1200,939 419,939" fill="url(#skyGradient)"/>
    <polygon class="photo-frame" points="846,0 1200,0 1200,372 1088,632 570,632" fill="var(--white)"/>
    <polygon class="photo" role="img" aria-label="Photo of a smiling senior couple embracing in a bright living room"
      points="862,0 1200,0 1200,380 1078,620 590,620" fill="url(#photoGradient)"/>
    <polygon class="services-panel" points="517,744 1200,744 1200,925 443,925" fill="url(#navyGradient)"/>
  </svg>

  <header class="brand">
    <div class="brand-row">
      <span class="brand-mark"></span>
      <div class="brand-name">RQ PRIVATE WEALTH<br>MANAGEMENT</div>
    </div>
    <div class="brand-team">MARCUS FENLEY<br>&amp; PARTNERS</div>
  </header>

  <h1 class="headline">
    <div class="headline-intro">Your wealth is<br>full of possibilities</div>
    <div class="headline-accent">Now you</div>
    <div class="headline-strong">Need a plan</div>
  </h1>

  <p class="industry">We are in the Wealth Management<br>or Financial Planning industry</p>

  <section class="clients">
    <h2 class="clients-title">WE DEAL WITH</h2>
    <ul class="clients-list">
      <li><svg class="tick" viewBox="0 0 24 24"><circle cx="12" cy="12" r="12" fill="#45b2f5"/><path d="M6.5 12.5l3.5 3.5 7.5-7.5" stroke="#fff" stroke-width="2.6" fill="none" stroke-linecap="round" stroke-linejoin="round"/></svg>High-net-worth retirees</li>
      <li><svg class="tick" viewBox="0 0 24 24"><circle cx="12" cy="12" r="12" fill="#45b2f5"/><path d="M6.5 12.5l3.5 3.5 7.5-7.5" stroke="#fff" stroke-width="2.6" fill="none" stroke-linecap="round" stroke-linejoin="round"/></svg>Business owners</li>
      <li><svg class="tick" viewBox="0 0 24 24"><circle cx="12" cy="12" r="12" fill="#45b2f5"/><path d="M6.5 12.5l3.5 3.5 7.5-7.5" stroke="#fff" stroke-width="2.6" fill="none" stroke-linecap="round" stroke-linejoin="round"/></svg>Farmers</li>
      <li><svg class="tick" viewBox="0 0 24 24"><circle cx="12" cy="12" r="12" fill="#45b2f5"/><path d="M6.5 12.5l3.5 3.5 7.5-7.5" stroke="#fff" stroke-width="2.6" fill="none" stroke-linecap="round" stroke-linejoin="round"/></svg>Wealth transfer</li>
    </ul>
  </section>

  <div class="offer-head">
    <h2 class="offer-title">WE OFFER</h2>
    <p class="offer-sub">High-net-worth client<br>solutions that cover</p>
  </div>

  <section class="services">
    <div class="service">
      <svg class="service-icon" viewBox="0 0 44 44"><circle cx="24" cy="12" r="10" fill="#fff"/><text x="24" y="17" text-anchor="middle" font-family="Poppins, sans-serif" font-weight="700" font-size="14" fill="#0b1c4d">$</text><path d="M4 32h8l8 4h12l8-6" stroke="#45b2f5" stroke-width="4" fill="none" stroke-linecap="round" stroke-linejoin="round"/></svg>
      Financial<br>Planning
    </div>
    <div class="service">
      <svg class="service-icon" viewBox="0 0 44 44"><circle cx="18" cy="10" r="9" fill="#fff"/><text x="18" y="15" text-anchor="middle" font-family="Poppins, sans-serif" font-weight="700" font-size="13" fill="#0b1c4d">$</text><path d="M30 8v22H12M14 30v8M30 30v8M8 40h28" stroke="#45b2f5" stroke-width="3" fill="none" stroke-linecap="round"/></svg>
      Retirement<br>&amp; Estate<br>Planning
    </div>
    <div class="service">
      <svg class="service-icon" viewBox="0 0 44 44"><circle cx="24" cy="16" r="10" fill="#fff"/><text x="24" y="21" text-anchor="middle" font-family="Poppins, sans-serif" font-weight="700" font-size="13" fill="#0b1c4d">$</text><path d="M6 12V4M3 7l3-3 3 3M40 12V4M37 7l3-3 3 3M4 38l10-8h10" stroke="#45b2f5" stroke-width="3" fill="none" stroke-linecap="round" stroke-linejoin="round"/></svg>
      Investment<br>Planning
    </div>
    <div class="service">
      <svg class="service-icon" viewBox="0 0 44 44"><rect x="16" y="4" width="22" height="34" rx="3" fill="#45b2f5"/><path d="M22 14h10M22 21h10M22 28h10" stroke="#fff" stroke-width="2.5"/><circle cx="14" cy="28" r="10" fill="#fff"/><text x="14" y="33" text-anchor="middle" font-family="Poppins, sans-serif" font-weight="700" font-size="12" fill="#0b1c4d">%</text></svg>
      Tax<br>Planning
    </div>
    <div class="service">
      <svg class="service-icon" viewBox="0 0 44 44"><path d="M4 18a18 14 0 0 1 36 0z" fill="#45b2f5"/><path d="M22 4v2M22 18v6" stroke="#45b2f5" stroke-width="2.5"/><circle cx="20" cy="32" r="9" fill="#fff"/><text x="20" y="37" text-anchor="middle" font-family="Poppins, sans-serif" font-weight="700" font-size="12" fill="#0b1c4d">$</text></svg>
      Insurance<br>Planning
    </div>
  </section>

  <section class="booking">
    <h2 class="booking-title">FOR ONLINE BOOKING VISIT THE LINK BELOW</h2>
    <p class="booking-link">https://calendar.brisquelmail.com/owa/calendar/MarcusFenleyPartnersRQPrivateWealth@tovrelfinancial.net/bookings/</p>
  </section>

  <footer class="contact">
    <div class="social"><span class="social-dot"></span>https://www.plorvenet.com/FenleyPrivateWealth</div>
    <span class="contact-divider"></span>
    <div class="website">www.<span>rqprivatewealth</span>.com</div>
  </footer>
</main>
</body>
</html>
```